Business Card Design

We need a business card designed for our new company. Prefer a black card with white logo & writing.

Contact Information for Business Card

Ted Galloway, address: 7-4812 Fernhollow Road, Abbotsford, BC, V3K 8R2, Office Phone: 604-712-3390, Cell: 604-947-2164, Email: ted@resinworkshub.ca

Colors

Designer to choose only greyscale colors for use in the design.

```html
<!DOCTYPE html>
<html lang="en">
<head>
<meta charset="utf-8">
<title>Resinworks Hub – Business Card</title>
<link href="https://fonts.googleapis.com/css2?family=Montserrat:wght@400;700&display=swap" rel="stylesheet">
<style>
  :root {
    --backdrop: #161616;
    --card-dark: #232323;
    --card-light: #ffffff;
    --ink-light: #ffffff;
    --ink-dark: #1f1f1f;
    --ink-muted: #e4e4e4;
    --emboss: #141414;
  }
  * { margin: 0; padding: 0; box-sizing: border-box; }
  html, body {
    width: 1200px; height: 1059px; overflow: hidden;
    background: var(--backdrop);
    font-family: "Montserrat", sans-serif;
  }
  .canvas { position: relative; width: 1200px; height: 1059px; }
  .card {
    position: absolute; left: 253px; width: 695px; height: 399px;
    border-radius: 22px; overflow: hidden;
  }
  .card--front { top: 89px; background: var(--card-light); }
  .card--back { top: 546px; background: var(--card-dark); }
  .card__wave { position: absolute; inset: 0; }
  .brand-name {
    position: absolute; font-weight: 700; letter-spacing: 1px;
    text-transform: uppercase; text-align: center; line-height: 1.1;
  }
  .card--front .brand-name {
    left: 455px; top: 80px; width: 200px; font-size: 24px; color: var(--ink-dark);
  }
  .card--back .brand-name {
    left: 0; right: 0; top: 150px; font-size: 50px; color: var(--emboss);
  }
  .person { position: absolute; left: 34px; top: 208px; color: var(--ink-light); }
  .person__name { font-size: 22px; font-weight: 700; }
  .person__role { font-size: 13px; color: var(--ink-muted); margin-top: 4px; }
  .contacts { position: absolute; left: 34px; top: 269px; list-style: none; }
  .contacts li {
    display: flex; align-items: center; height: 24px; margin-bottom: 0;
    font-size: 14px; color: var(--ink-light);
  }
  .contacts svg { width: 15px; height: 15px; margin-right: 12px; fill: var(--ink-light); }
  .address {
    position: absolute; left: 458px; top: 326px;
    font-size: 15px; line-height: 18px; color: var(--ink-light); font-style: normal;
  }
</style>
</head>
<body>
<main class="canvas">
  <section class="card card--front">
    <svg class="card__wave" viewBox="0 0 695 399" width="695" height="399" aria-hidden="true">
      <path d="M0,164 C70,118 170,112 290,160 C390,205 470,268 560,264 C620,262 670,228 695,178 L695,399 L0,399 Z" fill="var(--card-dark)"/>
      <path d="M0,196 C60,152 160,142 290,188 C400,230 480,300 570,302 C625,303 670,268 695,225" fill="none" stroke="var(--card-light)" stroke-width="4"/>
    </svg>
    <div class="brand-name">Resinworks<br>Hub</div>
    <div class="person">
      <div class="person__name">Ted Galloway</div>
      <div class="person__role">Owner</div>
    </div>
    <ul class="contacts">
      <li><svg viewBox="0 0 24 24"><path d="M6.6 10.8a15 15 0 0 0 6.6 6.6l2.2-2.2a1 1 0 0 1 1-.25 11.4 11.4 0 0 0 3.6.6 1 1 0 0 1 1 1V20a1 1 0 0 1-1 1A17 17 0 0 1 3 4a1 1 0 0 1 1-1h3.5a1 1 0 0 1 1 1c0 1.25.2 2.45.6 3.6a1 1 0 0 1-.25 1z"/></svg>604-712-3390</li>
      <li><svg viewBox="0 0 24 24"><path d="M7 1h10a2 2 0 0 1 2 2v18a2 2 0 0 1-2 2H7a2 2 0 0 1-2-2V3a2 2 0 0 1 2-2zm0 3v14h10V4zm5 15.5a1 1 0 1 0 0 2 1 1 0 0 0 0-2z"/></svg>604-947-2164</li>
      <li><svg viewBox="0 0 24 24"><path d="M2 5h20v14H2zm2 2v.5l8 5 8-5V7z"/></svg>ted@resinworkshub.ca</li>
      <li><svg viewBox="0 0 24 24"><path d="M12 2a10 10 0 1 0 0 20 10 10 0 0 0 0-20zm0 2a8 8 0 0 1 6.9 4H16l-2 3-3-1-2 3 2 3-1 4a8 8 0 0 1 2-16z"/></svg>www.resinworkshub.ca</li>
    </ul>
    <address class="address">7-4812 Fernhollow Road,<br>Abbotsford, BC, V3K 8R2</address>
  </section>

  <section class="card card--back">
    <div class="brand-name">Resinworks<br>Hub</div>
  </section>
</main>
</body>
</html>
```